Modern design company business card design

We are a design oriented construction firm. The owner is an architect and licensed General Contractor and accomplished furniture designer. We do new home construction and large scale remodeling and office design. We would like a design for our new business cards that is clean and modern, but relatable. We like the bright green color of our logo mixed with different shades of grey. We're also open to reinterpreting the logo.

Target Market(s)

Potential design clients,
Construction clients

Industry/Entity Type

Architecture

Contact Information for Business Card

Tall Maple Design | Build Inc. (optional with logo, Inc. optional)Jeffrey MorganOwner (optional)317.555.0148 cell317.431.8056 officejmorgan@greensquareinc.comwww.greensquareinc.com

Font styles to use
Sans Serif
Other font styles liked:
• Avenir

Requirements
Nice to have
• I like designs that have some continuity between the front and back, i.e. similar layouts or graphic elements that wrap around the card. I tend to prefer horizontal over vertical, but that's not a have to. I also tend to prefer white or recycled paper.

```html
<!DOCTYPE html>
<html lang="en">
<head>
<meta charset="utf-8">
<title>Tall Maple Design | Build – Business Card</title>
<link rel="stylesheet" href="https://fonts.googleapis.com/css2?family=Jost:ital,wght@0,400;0,500;1,400&display=swap">
<style>
  :root {
    --stage: #3b3b3b;
    --paper: #ffffff;
    --green: #7dc35b;
    --green-light: #c3dc6a;
    --green-text: #72be4a;
    --grey-dark: #4a4a4a;
    --grey-mid: #8a8a8a;
    --grey-rule: #b5b5b5;
  }
  * { margin: 0; padding: 0; box-sizing: border-box; }
  html, body {
    width: 1105px;
    height: 1200px;
    overflow: hidden;
    background: var(--stage);
    font-family: "Jost", "Avenir", sans-serif;
  }
  .canvas { position: relative; width: 1105px; height: 1200px; }

  .card {
    position: absolute;
    left: 196px;
    width: 719px;
    height: 412px;
  }
  .card--front { top: 146px; background: var(--paper); }
  .card--back {
    top: 602px;
    background: linear-gradient(180deg, var(--green-light) 0%, var(--green) 100%);
  }

  /* front: brand block */
  .brand-square {
    position: absolute;
    left: 542px;
    top: 29px;
    width: 141px;
    height: 141px;
    background: var(--green-light);
  }
  .brand-name {
    position: absolute;
    right: 36px;
    top: 174px;
    text-align: right;
    color: var(--grey-mid);
    font-weight: 400;
    line-height: 1;
  }
  .brand-name__primary { display: block; font-size: 29px; letter-spacing: 2px; }
  .brand-name__secondary { display: block; font-size: 16px; letter-spacing: 1px; margin-top: 8px; }

  /* front: person */
  .person { position: absolute; left: 36px; top: 248px; }
  .person__name {
    font-size: 29px;
    font-weight: 400;
    color: var(--green-text);
    letter-spacing: 0.3px;
    line-height: 1.1;
  }
  .person__role {
    font-size: 22px;
    font-weight: 400;
    color: var(--grey-dark);
    margin-top: 6px;
    line-height: 1;
  }

  .contact {
    position: absolute;
    left: 36px;
    top: 330px;
    display: flex;
    font-size: 19px;
    color: var(--grey-dark);
    line-height: 28px;
  }
  .contact__phones { padding-right: 12px; border-right: 2px solid var(--grey-rule); }
  .contact__online { padding-left: 14px; }

  /* back */
  .back-square {
    position: absolute;
    left: 282px;
    top: 132px;
    width: 155px;
    height: 155px;
    background: var(--paper);
  }
  .back-url {
    position: absolute;
    left: 0;
    right: 0;
    top: 342px;
    text-align: center;
    font-size: 18px;
    font-style: italic;
    letter-spacing: 2px;
    color: var(--paper);
  }
</style>
</head>
<body>
<main class="canvas">
  <section class="card card--front" aria-label="Business card front">
    <div class="brand-square"></div>
    <p class="brand-name">
      <span class="brand-name__primary">TALL MAPLE</span>
      <span class="brand-name__secondary">DESIGN | BUILD INC.</span>
    </p>

    <div class="person">
      <h1 class="person__name">DENNIS HOLLOWAY</h1>
      <p class="person__role">OWNER</p>
    </div>

    <div class="contact">
      <div class="contact__phones">
        <p>317.555.0148</p>
        <p>317.555.0172</p>
      </div>
      <div class="contact__online">
        <p>www.tallmapleinc.example</p>
        <p>dholloway@tallmapleinc.example</p>
      </div>
    </div>
  </section>

  <section class="card card--back" aria-label="Business card back">
    <div class="back-square"></div>
    <p class="back-url">www.tallmapleinc.example</p>
  </section>
</main>
</body>
</html>
```